Customer Value Leaflet

We need a bi-fold brochure designing, based on the attached PDF wireframes. Our company name is brambleharvik.com (of which the logo is currently being designed). The corporate colour is orange (the exact shade of which we are happy to leave to the designers discretion).

The leaflet will distributed to customer experience experts and marketers so the design needs to be bright, engaging, clean and simple. Design is critical.

It Company

```html
<!DOCTYPE html>
<html lang="en">
<head>
<meta charset="utf-8">
<title>Customer Value Leaflet</title>
<link rel="stylesheet" href="https://fonts.googleapis.com/css2?family=Carlito:wght@400;700&display=swap">
<style>
  :root {
    --paper: #ffffff;
    --ink: #000000;
    --brand-orange: #f7941d;
  }
  * { margin: 0; padding: 0; box-sizing: border-box; }
  html, body {
    width: 1200px;
    height: 1200px;
    overflow: hidden;
    background: var(--paper);
  }
  .leaflet-panel {
    position: relative;
    width: 1200px;
    height: 1200px;
    background: var(--paper);
    color: var(--ink);
    font-family: "Carlito", "Calibri", sans-serif;
  }
  .headline-lead {
    position: absolute;
    left: 56px;
    top: 212px;
    font-weight: 700;
    font-size: 62px;
    line-height: 90px;
    letter-spacing: -0.2px;
  }
  .highlight-term {
    color: var(--brand-orange);
    text-decoration: underline;
    text-decoration-thickness: 4px;
    text-underline-offset: 7px;
  }
  .headline-payoff {
    position: absolute;
    right: 64px;
    top: 600px;
    text-align: right;
    font-weight: 700;
    font-size: 64px;
    line-height: 96px;
    letter-spacing: -0.2px;
  }
  .site-callout {
    position: absolute;
    left: 88px;
    top: 1048px;
    font-size: 46px;
    line-height: 70px;
    font-weight: 400;
  }
  .site-address {
    font-weight: 700;
    font-size: 52px;
  }
</style>
</head>
<body>
  <main class="leaflet-panel">
    <h1 class="headline-lead">By predicting <span class="highlight-term">Customer Lifetime <br>Value</span> today…</h1>
    <p class="headline-payoff">…you can optimise<br>your business for tomorrow</p>
    <p class="site-callout">Find our more at <span class="site-address">www.brambleharvik.com</span></p>
  </main>
</body>
</html>
```